Website development company website

ABOUT COMPANY
Hi everyone! We're a Melbourne, Australia website development company in a need of a website design that will make online store merchants want to engage our services.
We specialise exclusively in Torvista e-commerce platform (https://torvista-platform.example/). What distinguishes our business from competition is that rather than designing and building brand new websites, we offer development, support and maintenance services to established websites. Maintenance and Support are the keywords representing our business.
Our potential clients are people with broken, slow and underperforming Torvista installations who need assistance getting their websites up and making sales. Our website must pass the message that we can help, and provide quick means of making contact.
DESIGN
Overall, we're looking for a slick, clean, airy, conservative design. No need to do anything crazy, try to stick to what's "standard" in website design these days and make it easy on all of us. The website is unlikely to be updated too often so it needs to look attractive and fresh first time over and after a year, too.
Attached is our new logo, which you'll be able to take the basic idea from, the colors and fonts. Though, don't use the fonts from the logo in the website, stick to the standard widely supported fonts. Additional use of Google fonts is fine.
Don't overdo it with colors, stick to conservative basic color set and only use the colors from the log for accents like headings etc. Please, don't be tempted to use the blue and orange as background of whole blocks, other than perhaps footer. Thanks.
For the images used, I'd like to stay away from a design studio/digital agency feel and lean more towards professional support and maintenance services. I'm thinking images of content merchants doing their job. Something along the lines of "We'll be taking care of the website so that you only need to care about the business".
Some ideas I like:
http://www.plumframe-pics.example/detail/photo/portrait-of-confident-male-design-professional-royalty-free-image/572048163
http://www.plumframe-pics.example/detail/photo/designer-taking-picture-of-hat-high-res-stock-photography/839207514
http://www.plumframe-pics.example/detail/photo/woman-packaging-pottery-royalty-free-image/216684093
Images of colorful shopping bags and shopping carts are over the top and not serious enough. Instead of images matching Online Shopping, I'd try going more for Stability, Reliability, Performance.
Our existing website is http://www.bravuln.example. Please, don't take design ideas from it, but it will give you a picture of the structure of our new website and content that's going to be used initially.
If you could include a basic icon set to use throughout the website, that would be great. If the icons could match our logo (attached), it would be a big plus.
ALL PAGES
Every page must contain clearly visible phone number (1300 648 907) and a Contact Us Now button, which opens an AJAX driven popup form with Name, Email, Phone and Message to be sent through.
To start with, main menu items will be Torvista, Portfolio, Contact.
At the bottom of each page, please, include a newsletter subscription form with text Subscribe to Torvista Support and Security Updates.
For the footer, I'd like to see a logo strip with the following logos in grayscale (no need to link anywhere): Torvista, QRX, DataVane, NCB. You'll find the logos on Google Images.
Standard footer columns follow. Here, I'd like to see logos in color: Torvista Certified Developer, Torvista Ceritified Solution Provider. Again, the logos are on Google Images.
No social media logos/links necessary anywhere on the website.
...and then the copyright line.
FRONT PAGE
Large slider with images that would appeal to our target audience. Keywords here would be Torvista System Audit, Torvista Performance Optimisation, Torvista Website Emergency Recovery, Torvista Development Infrastructure Hosting. We'll have a static page created for each of these to link to.
In a corner of the slider, or on the edge, can I have an overlay with logos in color (same as footer): Torvista Certified Developer, Torvista Ceritified Solution Provider.
Underneath, a number of blocks, each with an image and teaser that we'll use to link to various pages throughout the website.
PORTFOLIO PAGE
I'm thinking a single long page with a block per client, which will contain project name, description from us and a testimonial from client. Also, each block will contain a single large screenshot. No gallery or slideshow is necessary here, just one image per project.
I'll leave the layout up to you, but try to put yourself in the shoes of a potential client reviewing our past work by simply scrolling down this one page.
CONTACT US PAGE
Separate page with the same form as above, phone number (1300 648 907), email address (support@kavreo.example), address (Suite 42, Level 3|8 Wattlebrook Lane|Fernvale Heights VIC 3999), and a grayscale Google Map.
CODING UP
Coding up into static HTML/CSS/JS is equally important as the design itself. We're a website development company, we'll be integrating the theme. We will spot any issues and we will point them out.
Coded up design must be fully responsive. Enough said.
To be able to create any content in future, we'd like one extra page coded up with samples of all themed elements, lists, forms, buttons, 2, 3, 4-column layout, alerts, icons, etc. This page does not need to be designed, only coded up.
The design will be integrated into Drupal using Twig. If possible at all, try to keep it in mind when designing and coding up, and make the integration into a Drupal theme easier for us.
GOOD LUCK!
That's it. Let me know if anything needs clarifying. So far I've had a great experience with ArtFlockly. I don't doubt some great designs will emerge. Clever ideas are highly appreciated, but also make it clear you've read and followed the points in this brief. Cheers, Tom

```html
<!DOCTYPE html>
<html lang="en">
<head>
<meta charset="utf-8">
<title>Kavreo E-Commerce</title>
<link rel="stylesheet" href="https://fonts.googleapis.com/css2?family=Bebas+Neue&family=Open+Sans:wght@400;600;700&family=Raleway:wght@400;500;600&family=Roboto+Condensed:wght@400;700&display=swap">
<style>
:root{
  --navy:#173a66;
  --orange:#e67e22;
  --text:#5f5f5f;
  --topbar:#efefef;
  --band:#e4e4e4;
  --footer:#1e1e1e;
  --white:#ffffff;
}
*{box-sizing:border-box;margin:0;padding:0}
html,body{width:741px;height:1200px;overflow:hidden;background:var(--white)}
body{position:relative;font-family:"Open Sans",sans-serif;color:var(--text)}
.topbar{position:absolute;top:0;left:0;width:741px;height:26px;background:var(--topbar);border-bottom:1px solid #dcdcdc}
.topbar-help{position:absolute;right:48px;top:6px;display:flex;align-items:center;gap:6px;font-family:"Roboto Condensed",sans-serif;font-size:11.5px}
.topbar-help .label{color:var(--orange);margin-right:4px}
.topbar-help .phone{color:var(--navy);font-weight:700}
.header{position:absolute;top:26px;left:0;width:741px;height:77px;background:var(--white)}
.brand{position:absolute;left:48px;top:18px;display:flex;align-items:center;gap:8px}
.brand-mark{width:28px;height:40px;background:var(--navy)}
.brand-name{font-family:"Raleway",sans-serif;font-weight:600;font-size:27px;color:var(--navy);line-height:1}
.nav{position:absolute;right:48px;top:17px;display:flex;align-items:center;font-family:"Raleway",sans-serif;font-size:12.5px}
.nav a{color:#555;text-decoration:none;margin-left:30px}
.nav a.active{color:var(--navy)}
.nav a.btn-contact{background:var(--orange);color:var(--white);padding:8px 15px;margin-left:16px}
.hero{position:absolute;top:103px;left:0;width:741px;height:354px;background:linear-gradient(100deg,#c7cdd2 0%,#e1e3e3 35%,#d8d6d2 60%,#b9bec2 100%)}
.hero-title{position:absolute;top:98px;left:0;width:741px;text-align:center;font-family:"Bebas Neue",sans-serif;font-size:35px;line-height:45px;color:var(--navy);letter-spacing:.3px}
.hero-btn{position:absolute;left:283px;top:201px;width:174px;height:45px;background:var(--orange);color:var(--white);font-family:"Raleway",sans-serif;font-size:16px;display:flex;align-items:center;justify-content:center;border-radius:2px}
.welcome{position:absolute;top:457px;left:0;width:741px;height:211px;text-align:center}
.section-title{font-family:"Raleway",sans-serif;font-weight:400;font-size:26px;color:var(--navy);letter-spacing:.2px}
.section-title .accent{color:var(--orange)}
.welcome .section-title{position:absolute;top:33px;width:100%}
.welcome-text{position:absolute;top:72px;left:100px;width:541px;font-size:10px;line-height:15.5px;color:var(--text)}
.btn-outline{position:absolute;left:311px;top:136px;width:119px;height:33px;border:1px solid var(--navy);color:var(--navy);font-family:"Raleway",sans-serif;font-size:14px;display:flex;align-items:center;justify-content:center}
.services{position:absolute;top:668px;left:0;width:741px;height:289px;background:var(--band)}
.services .section-title{position:absolute;top:30px;width:100%;text-align:center}
.service{position:absolute;top:73px;width:192px;text-align:center}
.service-media{width:192px;height:97px}
.service-media.platform{background:linear-gradient(180deg,#f5f5f5,#dedede);border:1px solid #b9b9b9;display:flex;align-items:center;justify-content:center;font-family:"Raleway",sans-serif;font-weight:500;font-size:26px;color:#333}
.service-media.support{background:linear-gradient(120deg,#e9ecef,#c9ced3 55%,#8f9aa4)}
.service-media.upkeep{background:linear-gradient(120deg,#d7d9d8,#9ba3a8 50%,#4f5963)}
.service-title{margin-top:11px;font-family:"Raleway",sans-serif;font-size:16px;color:var(--navy)}
.service-text{margin-top:7px;font-size:10px;line-height:15.5px;color:var(--text)}
.tech-strip{position:absolute;top:957px;left:0;width:741px;height:88px;background:var(--white);display:flex;align-items:center;justify-content:space-around;padding:0 70px}
.tech-strip span{font-family:"Raleway",sans-serif;font-weight:500;font-size:22px;color:#8a8a8a}
.footer{position:absolute;top:1045px;left:0;width:741px;height:155px;background:var(--footer);color:#e8e8e8}
.footer-col{position:absolute;top:20px;font-size:10px;line-height:15.5px}
.footer-heading{font-family:"Roboto Condensed",sans-serif;font-size:13px;color:var(--orange);letter-spacing:.3px;margin-bottom:8px}
.footer-row{display:flex;gap:8px}
.footer-row svg{flex:none;margin-top:2px}
.footer-col a{color:var(--orange)}
.footer-phone{font-family:"Roboto Condensed",sans-serif;font-weight:700;font-size:12px;color:var(--white)}
.newsletter{display:flex;margin-top:9px}
.newsletter .field{width:110px;height:26px;background:var(--white);color:#777;font-size:10px;padding:6px 6px}
.newsletter .submit{width:83px;height:26px;background:var(--navy);color:var(--white);font-family:"Roboto Condensed",sans-serif;font-size:13px;display:flex;align-items:center;justify-content:center}
.footer-rule{position:absolute;left:48px;top:122px;width:645px;height:1px;background:#3a3a3a}
.copyright{position:absolute;top:131px;width:100%;text-align:center;font-size:9.5px;color:#cfcfcf}
.copyright strong{color:var(--orange);font-weight:700}
</style>
</head>
<body>

<div class="topbar">
  <div class="topbar-help">
    <span class="label">WE CAN HELP YOU</span>
    <svg width="12" height="12" viewBox="0 0 24 24"><path fill="#173a66" d="M6.6 10.8a15.1 15.1 0 006.6 6.6l2.2-2.2c.3-.3.7-.4 1-.2 1.1.4 2.3.6 3.6.6.6 0 1 .4 1 1V20c0 .6-.4 1-1 1A17 17 0 013 4c0-.6.4-1 1-1h3.5c.6 0 1 .4 1 1 0 1.3.2 2.5.6 3.6.1.3 0 .7-.2 1z"/></svg>
    <span class="phone">1300 648 907</span>
  </div>
</div>

<header class="header">
  <div class="brand">
    <div class="brand-mark"></div>
    <div class="brand-name">Kavreo</div>
  </div>
  <nav class="nav">
    <a class="active">HOME</a>
    <a>ABOUT</a>
    <a>TORVISTA</a>
    <a>PORTFOLIO</a>
    <a class="btn-contact">CONTACT</a>
  </nav>
</header>

<section class="hero" role="img" aria-label="Photo of business people meeting around an office table with laptops and printed charts">
  <h1 class="hero-title">We will be taking care of the website so that<br>you only need to care about the business</h1>
  <div class="hero-btn">CONTACT US NOW</div>
</section>

<section class="welcome">
  <h2 class="section-title"><span class="accent">WELCOME TO</span> KAVREO E-COMMERCE</h2>
  <p class="welcome-text">Lorem Ipsum is simply dummy text of the printing and typesetting industry. Lorem Ipsum has been the industry's standard dummy text ever since the 1500s, when an unknown printer took a galley of type and scrambled it to make a type specimen book.</p>
  <div class="btn-outline">READ MORE</div>
</section>

<section class="services">
  <h2 class="section-title"><span class="accent">OUR</span> SERVICES</h2>
  <div class="service" style="left:48px">
    <div class="service-media platform">Torvista</div>
    <h3 class="service-title">DEVELOPMENT</h3>
    <p class="service-text">Lorem Ipsum is simply dummy text of the printing and typesetting industry. Lorem Ipsum has been the industry.</p>
  </div>
  <div class="service" style="left:274px">
    <div class="service-media support" role="img" aria-label="Photo of a smiling support agent wearing a headset with colleagues behind"></div>
    <h3 class="service-title">SUPPORT</h3>
    <p class="service-text">Lorem Ipsum is simply dummy text of the printing and typesetting industry. Lorem Ipsum has been the industry.</p>
  </div>
  <div class="service" style="left:501px">
    <div class="service-media upkeep" role="img" aria-label="Photo of two businessmen reviewing work on a laptop"></div>
    <h3 class="service-title">MAINTENANCE</h3>
    <p class="service-text">Lorem Ipsum is simply dummy text of the printing and typesetting industry. Lorem Ipsum has been the industry.</p>
  </div>
</section>

<section class="tech-strip">
  <span>Torvista</span>
  <span>DataVane</span>
  <span>QRX</span>
  <span>NCB</span>
</section>

<footer class="footer">
  <div class="footer-col" style="left:49px;width:200px">
    <h4 class="footer-heading">OUR LOCATION</h4>
    <div class="footer-row">
      <svg width="10" height="13" viewBox="0 0 24 32"><path fill="#fff" d="M12 0C5.4 0 0 5.4 0 12c0 9 12 20 12 20s12-11 12-20C24 5.4 18.6 0 12 0zm0 17a5 5 0 110-10 5 5 0 010 10z"/></svg>
      <div>Suite 42, Level 3, Brightwell Building<br>8 Wattlebrook Lane<br>Fernvale Heights VIC 3999<br><a>VIEW MAP</a></div>
    </div>
  </div>
  <div class="footer-col" style="left:277px;width:200px">
    <h4 class="footer-heading">OUR LOCATION</h4>
    <div class="footer-row" style="margin-top:14px;align-items:center">
      <svg width="13" height="13" viewBox="0 0 24 24"><path fill="#e67e22" d="M6.6 10.8a15.1 15.1 0 006.6 6.6l2.2-2.2c.3-.3.7-.4 1-.2 1.1.4 2.3.6 3.6.6.6 0 1 .4 1 1V20c0 .6-.4 1-1 1A17 17 0 013 4c0-.6.4-1 1-1h3.5c.6 0 1 .4 1 1 0 1.3.2 2.5.6 3.6.1.3 0 .7-.2 1z"/></svg>
      <span class="footer-phone">1300 648 907</span>
    </div>
    <div class="footer-row" style="margin-top:4px;align-items:center">
      <svg width="13" height="10" viewBox="0 0 26 20"><rect x="1" y="1" width="24" height="18" fill="none" stroke="#e67e22" stroke-width="2"/><path d="M1 1l12 10L25 1" fill="none" stroke="#e67e22" stroke-width="2"/></svg>
      <span>info@kavreo.example</span>
    </div>
  </div>
  <div class="footer-col" style="left:502px;width:200px">
    <h4 class="footer-heading">NEWSLETTER</h4>
    <p>Subscribe to Torvista Support and Security Updates</p>
    <div class="newsletter">
      <div class="field">Enter Email Id</div>
      <div class="submit">SUBSCRIBE</div>
    </div>
  </div>
  <div class="footer-rule"></div>
  <p class="copyright">© <strong>Kavreo E-commerce</strong> - 2016. All Rights Reserved.</p>
</footer>

</body>
</html>
```